Business Card for Multi-Brand Sportswear Company

We are looking for a business card which represents our company and the multiple brands within it.

The company: Fen Athletics (LTD)
The brands: Fen, TavaPuni, ElmStretch, Grit and Rain

Employees using these cards would be representing Fen Athletics, rather than any of the individual brands. You will see a current design within the uploaded files, to give some inspiration. The actual text of the brands is not necessary, but the logos should be on there is some format.

Our creative minds on this are stretched, so we are looking for someone to make this their own, and show us what a good business card should look like.

We may like to get these printed with spot gloss, so keep that in mind with your designs.

www.fenathletics.co.uk

Industry/Entity Type

Business

Contact Information for Business Card

Leo Pemberton-Hale
Operations Manager
(+44) 1632 960 418
Leo@fenathletics.co.uk
www.fenathletics.co.uk

Font styles to use
Sans Serif
Other font styles liked:
• Eurostile

Colors
ffffff

Requirements
Nice to have
• Dark (black) background

```html
<!DOCTYPE html>
<html lang="en">
<head>
<meta charset="utf-8">
<title>Fen Athletics – Business Card</title>
<link rel="stylesheet" href="https://fonts.googleapis.com/css2?family=Open+Sans:wght@400;600;700&display=swap">
<style>
  :root {
    --backdrop: #e9e6e3;
    --card: #1f2a33;
    --ink: #ffffff;
    --ink-soft: #e3e7ea;
    --rule: #8a949c;
  }
  * { margin: 0; padding: 0; box-sizing: border-box; }
  html, body {
    width: 1200px; height: 900px; overflow: hidden;
    background: var(--backdrop);
    font-family: "Open Sans", Arial, sans-serif;
    color: var(--ink);
  }
  .canvas { position: relative; width: 1200px; height: 900px; }
  .card {
    position: absolute; width: 555px; height: 343px;
    background: var(--card);
    box-shadow: 0 6px 18px rgba(0,0,0,0.25);
  }
  .card--front { left: 238px; top: 62px; }
  .card--back { left: 459px; top: 518px; }

  .wordmark {
    font-weight: 700; color: var(--ink); letter-spacing: 1px; line-height: 1;
  }
  .card--front .wordmark {
    position: absolute; left: 40px; top: 172px; font-size: 66px;
  }
  .contact { position: absolute; left: 314px; top: 86px; }
  .contact__name { font-size: 18px; font-weight: 600; line-height: 24px; }
  .contact__role { font-size: 15px; line-height: 20px; color: var(--ink-soft); }
  .contact__address { margin-top: 13px; font-size: 14.5px; line-height: 20px; color: var(--ink-soft); }
  .contact__lines { margin-top: 13px; list-style: none; }
  .contact__lines li {
    display: flex; align-items: center; gap: 8px;
    font-size: 14.5px; line-height: 20px; color: var(--ink-soft);
  }
  .contact__lines svg { width: 12px; height: 12px; fill: var(--ink-soft); flex: none; }

  .brand-lockup {
    position: absolute; left: 0; right: 0; top: 128px;
    display: flex; flex-direction: column; align-items: center;
  }
  .brand-lockup .wordmark { font-size: 44px; }
  .brand-lockup__tagline {
    margin-top: 6px; font-size: 9px; font-weight: 600; letter-spacing: 2px; color: var(--ink-soft);
  }
  .brand-row {
    position: absolute; left: 0; right: 0; top: 258px;
    display: flex; align-items: center; justify-content: center; gap: 14px;
  }
  .brand-row__rule { height: 1px; width: 142px; background: var(--rule); }
  .brand-row__names { display: flex; gap: 16px; }
  .brand-row__name { font-size: 12px; font-weight: 600; color: var(--ink); white-space: nowrap; }
</style>
</head>
<body>
<main class="canvas">
  <section class="card card--front" aria-label="Business card front">
    <div class="wordmark">Fen</div>
    <div class="contact">
      <p class="contact__name">Jonathan Smith</p>
      <p class="contact__role">Managing Director</p>
      <p class="contact__address">12345, Address Goes Here<br>Country Name, 123456.</p>
      <ul class="contact__lines">
        <li><svg viewBox="0 0 24 24" aria-hidden="true"><path d="M6.6 10.8a15.1 15.1 0 0 0 6.6 6.6l2.2-2.2c.3-.3.7-.4 1-.2 1.1.4 2.3.6 3.6.6.6 0 1 .4 1 1V20c0 .6-.4 1-1 1A17 17 0 0 1 3 4c0-.6.4-1 1-1h3.5c.6 0 1 .4 1 1 0 1.3.2 2.5.6 3.6.1.3 0 .7-.2 1z"/></svg>044-123 456 789</li>
        <li><svg viewBox="0 0 24 24" aria-hidden="true"><path d="M3 5h18v14H3z M4 6.5v1l8 5 8-5v-1z" fill-rule="evenodd"/></svg>info@webname.com</li>
        <li><svg viewBox="0 0 24 24" aria-hidden="true"><circle cx="12" cy="12" r="10"/></svg>www.websitename.com</li>
      </ul>
    </div>
  </section>

  <section class="card card--back" aria-label="Business card back">
    <div class="brand-lockup">
      <div class="wordmark">Fen Athletics</div>
      <p class="brand-lockup__tagline">PERFORMANCE WEAR</p>
    </div>
    <div class="brand-row">
      <span class="brand-row__rule"></span>
      <div class="brand-row__names">
        <span class="brand-row__name">Grit and Rain</span>
        <span class="brand-row__name">TavaPuni</span>
        <span class="brand-row__name">ElmStretch</span>
        <span class="brand-row__name">Fen</span>
      </div>
      <span class="brand-row__rule"></span>
    </div>
  </section>
</main>
</body>
</html>
```